Stationery for a private security company, "Brenmoor Security Services Ltd."

Needed is a stationery design for a private security company. The designs must show professionalism and that our company mean nothing but business. Watermark of the company logo on the letterhead page is also a must. The final design must represent innovation and professionalism. It would be great if designers could integrate the colours black and silver onto the cards and letterheads..

Thank you

```html
<!DOCTYPE html>
<html lang="en">
<head>
<meta charset="utf-8">
<title>Brenmoor Security Services Ltd. — Stationery</title>
<link rel="stylesheet" href="https://fonts.googleapis.com/css2?family=Cinzel:wght@700&family=Open+Sans:wght@400;700&display=swap">
<style>
  :root {
    --black: #0d0d0d;
    --charcoal: #2b2b2b;
    --silver: #a3a3a3;
    --silver-light: #cfcfcf;
    --paper: #ffffff;
    --backdrop: #ecedee;
    --ink: #3a3a3a;
    --watermark: #f1f1f1;
    --mark: "Cinzel", serif;
    --text: "Open Sans", sans-serif;
  }
  * { box-sizing: border-box; margin: 0; padding: 0; }
  html, body { width: 1200px; height: 937px; overflow: hidden; }
  body { background: var(--backdrop); position: relative; font-family: var(--text); color: var(--ink); }

  .sheet { position: absolute; background: var(--paper); overflow: hidden; }

  .wordmark { font-family: var(--mark); font-weight: 700; color: var(--black); line-height: 1; }
  .wordmark .name { display: block; letter-spacing: .04em; }
  .wordmark .sub { display: block; }

  /* Letterhead */
  .letterhead { left: 184px; top: 66px; width: 386px; height: 546px; }
  .letterhead .wordmark { position: absolute; left: 36px; top: 80px; }
  .letterhead .wordmark .name { font-size: 15px; }
  .letterhead .wordmark .sub { font-size: 6.4px; margin-top: 2px; }
  .letter-watermark { position: absolute; left: 0; top: 250px; width: 100%; text-align: center; font-family: var(--mark); font-weight: 700; font-size: 58px; letter-spacing: .04em; color: var(--watermark); line-height: 1; }
  .letter { position: absolute; left: 37px; top: 140px; width: 296px; font-size: 5px; line-height: 1.55; color: #555; }
  .letter p { margin-bottom: 9px; }
  .letter .salute { font-weight: 700; color: var(--ink); margin-bottom: 0; }
  .letter .para-gap { margin-bottom: 22px; }
  .signature { width: 44px; height: 16px; background: #e4e4e4; margin: 4px 0 6px; }
  .signer { font-weight: 700; color: var(--ink); }
  .letter-footer { position: absolute; left: 0; top: 484px; width: 100%; height: 42px; display: flex; font-size: 5.6px; line-height: 1.35; }
  .letter-footer .phone { width: 84px; background: var(--silver); color: #fff; padding: 7px 0 0 18px; white-space: nowrap; }
  .letter-footer .web { width: 112px; background: var(--charcoal); color: #d8d8d8; padding: 7px 0 0 10px; white-space: nowrap; }
  .letter-footer .address { flex: 1; background: var(--black); color: #fff; font-weight: 700; text-align: center; padding-top: 11px; font-size: 6.2px; }
  .label { font-weight: 700; letter-spacing: .03em; }

  /* Folder */
  .folder { left: 636px; top: 40px; width: 458px; height: 576px; }
  .folder .wordmark { position: absolute; top: 98px; width: 100%; text-align: center; }
  .folder .wordmark .name { font-size: 44px; letter-spacing: .08em; }
  .folder .wordmark .sub { font-size: 18px; margin-top: 6px; }
  .folder-art { position: absolute; left: 0; top: 222px; width: 100%; height: 250px; background: linear-gradient(135deg, #f4f4f4 0%, #d6d6d6 55%, #bdbdbd 100%); }
  .folder-band { position: absolute; left: 0; top: 473px; width: 100%; height: 50px; display: flex; }
  .folder-band .url { width: 58%; background: var(--silver); color: #fff; font-size: 9px; letter-spacing: .32em; display: flex; align-items: center; justify-content: center; }
  .folder-band .url b { font-weight: 700; }
  .folder-band .end { flex: 1; background: var(--black); }

  /* Business cards */
  .card { left: 45px; width: 177px; height: 100px; border-radius: 8px; }
  .card-front { top: 658px; }
  .card-front .holder { text-align: center; font-size: 8px; margin-top: 14px; color: var(--ink); letter-spacing: .03em; }
  .card-front .role { text-align: center; font-size: 4.6px; font-weight: 700; margin-top: 1px; }
  .card-band { position: absolute; top: 38px; left: 0; width: 100%; height: 28px; display: flex; font-size: 4.6px; line-height: 1.3; }
  .card-band .phone { width: 14px; background: var(--paper); }
  .card-band .phone-info { width: 78px; background: var(--silver); color: #fff; padding: 5px 0 0 10px; }
  .card-band .web { flex: 1; background: var(--black); color: #fff; padding: 5px 0 0 7px; white-space: nowrap; }
  .card-front .address { position: absolute; top: 73px; width: 100%; text-align: center; font-size: 4.6px; line-height: 1.45; }
  .card-back { top: 782px; }
  .card-back .strip { position: absolute; top: 35px; left: 0; width: 100%; height: 24px; display: flex; align-items: stretch; }
  .card-back .wordmark { width: 86px; padding: 5px 0 0 6px; }
  .card-back .wordmark .name { font-size: 9px; }
  .card-back .wordmark .sub { font-size: 3.6px; margin-top: 1px; }
  .card-back .url { width: 66px; background: var(--silver); color: #fff; font-size: 3.8px; display: flex; align-items: center; padding-left: 4px; }
  .card-back .end { flex: 1; background: var(--black); }

  /* Envelopes */
  .envelope { top: 672px; width: 431px; height: 207px; }
  .envelope-front { left: 265px; }
  .envelope-front .wordmark { position: absolute; left: 20px; top: 28px; }
  .envelope-front .wordmark .name { font-size: 15px; }
  .envelope-front .wordmark .sub { font-size: 6.4px; margin-top: 2px; }
  .envelope-back { left: 737px; }
  .flap { position: absolute; left: 0; top: 0; width: 100%; height: 72px; background: var(--black); border-radius: 0 0 28px 28px; color: #fff; font-size: 11px; letter-spacing: .2em; text-align: center; padding-top: 28px; }
  .envelope-back .wordmark { position: absolute; top: 124px; width: 100%; text-align: center; }
  .envelope-back .wordmark .name { font-size: 15px; }
  .envelope-back .wordmark .sub { font-size: 6.4px; margin-top: 2px; }
</style>
</head>
<body>

<section class="sheet letterhead">
  <div class="letter-watermark" aria-hidden="true">BRENMOOR</div>
  <div class="wordmark"><span class="name">Brenmoor</span><span class="sub">Security Services Ltd.</span></div>
  <div class="letter">
    <p>July 2, 2012</p>
    <p class="salute">Dear Sir,</p>
    <p>Carlow House, Mill St., United Kingdom</p>
    <p class="para-gap">We are pleased to confirm our proposal for guarding, patrol and access control services at your premises. Our licensed officers operate under a clear chain of command, with trained supervisors on every shift and full incident reporting. Each assignment begins with a site survey and a written risk assessment, followed by a security plan agreed with your facilities team before any officer is deployed.</p>
    <p class="para-gap">Our control room monitors every site around the clock, and response units are on call to support officers whenever needed.</p>
    <p>Please find enclosed our schedule of rates, insurance certificates and officer licensing details. We would welcome the chance to walk the site with you and answer any questions about staffing levels, reporting or our vetting process. Our account manager will contact you this week to arrange a convenient time for that visit.</p>
    <p>Best Regards,</p>
    <div class="signature" role="img" aria-label="Handwritten signature"></div>
    <p style="margin-bottom:0"><span class="signer">Daniel Hart</span><br>Director<br><br>Carlow House, Mill St., United Kingdom</p>
  </div>
  <footer class="letter-footer">
    <div class="phone"><span class="label">PHONE &amp; FAX</span><br>+44 20 7946 0132<br>+44 20 7946 0133</div>
    <div class="web"><span class="label">EMAIL &amp; WEB</span><br>office@brenmoorsecurity.com<br>www.brenmoorsecurity.com</div>
    <div class="address">48 HARROW LANE, KESTFORD KT4 9PL<br>UNITED KINGDOM</div>
  </footer>
</section>

<section class="sheet folder">
  <div class="wordmark"><span class="name">Brenmoor</span><span class="sub">Security Services Ltd.</span></div>
  <div class="folder-art" role="img" aria-label="Large brand emblem artwork in black and silver"></div>
  <div class="folder-band">
    <div class="url">WWW.<b>BRENMOORSECURITY</b>.COM</div>
    <div class="end"></div>
  </div>
</section>

<section class="sheet card card-front">
  <p class="holder">OLIVER <b>REYES</b></p>
  <p class="role">SENIOR SECURITY CONSULTANT</p>
  <div class="card-band">
    <div class="phone"></div>
    <div class="phone-info"><span class="label">PHONE &amp; FAX</span><br>+44 20 7946 0132<br>+44 20 7946 0133</div>
    <div class="web"><span class="label">EMAIL &amp; WEB</span><br>office@brenmoorsecurity.com<br>www.brenmoorsecurity.com</div>
  </div>
  <p class="address">48 <b>HARROW LANE</b>, KESTFORD <b>KT4 9PL</b><br><b>UNITED KINGDOM</b></p>
</section>

<section class="sheet card card-back">
  <div class="strip">
    <div class="wordmark"><span class="name">Brenmoor</span><span class="sub">Security Services Ltd.</span></div>
    <div class="url">www.brenmoorsecurity.com</div>
    <div class="end"></div>
  </div>
</section>

<section class="sheet envelope envelope-front">
  <div class="wordmark"><span class="name">Brenmoor</span><span class="sub">Security Services Ltd.</span></div>
</section>

<section class="sheet envelope envelope-back">
  <div class="flap">www.brenmoorsecurity.com</div>
  <div class="wordmark"><span class="name">Brenmoor</span><span class="sub">Security Services Ltd.</span></div>
</section>

</body>
</html>
```